Business card for Eyelash extension salon in Beverly Hills,California USA

We need new business card for our salon in Beverly Hills. The salon name is 'Lashvera' . We would like to have...Business name: Lashvera Name of person: will provide later Address 4720 N.Alder Crest Ave Linden Vale , CA 91827 Phone: will provide later (Text only) Web: www.lashverastudio.example Snapgrid icon, Circlebook icon follow us for seasonal campaign and news @lashverastudiolounge Design should look elegant, high-end, clean, simple, cohesive with my brand. Please refer my brand board. Business name color will be metallic bronzy color. Im thinking grey background or white background. Thanks

Target Market(s)

25-35. Gender neutral. People who are in Entertainment business industry.
This is High-end Eyelash extension salon in Beverly Hills

Industry/Entity Type

Beauty Salon

Contact Information for Business Card

Business name: Lashvera
Name of person: will provide later
Address 4720 N.Alder Crest Ave Linden Vale , CA 91827
Phone: will provide later (Text only)
Web: www.lashverastudio.example
Snapgrid icon, Circlebook icon
follow us for seasonal campaign and news @lashverastudiolounge

Requirements
Must have
• Beautiful, elegant, clean and simple look but very attractive and modern
Should not have
• We don't like too clutter, too busy designs.

```html
<!DOCTYPE html>
<html lang="en">
<head>
<meta charset="utf-8">
<title>Lashvera Business Card</title>
<link href="https://fonts.googleapis.com/css2?family=Bodoni+Moda:wght@500;600&family=Gilda+Display&display=swap" rel="stylesheet">
<style>
  :root {
    --backdrop: #dcdcdc;
    --card-light: #ffffff;
    --card-dark: #000000;
    --bronze: #7d6054;
    --rule: #8e776d;
    --logo-ink: #ffffff;
  }
  * { margin: 0; padding: 0; box-sizing: border-box; }
  html, body {
    width: 1200px;
    height: 930px;
    overflow: hidden;
    background: var(--backdrop);
  }
  .card {
    position: absolute;
    width: 564px;
    height: 323px;
  }
  .card--front { left: 318px; top: 125px; background: var(--card-light); }
  .card--back  { left: 318px; top: 514px; background: var(--card-dark); }

  .frame-line {
    position: absolute;
    background: var(--rule);
  }
  .frame-line--top    { left: 37px; top: 37px; width: 286px; height: 1px; }
  .frame-line--side   { left: 37px; top: 37px; width: 1px; height: 87px; }
  .frame-line--bottom { left: 80px; top: 289px; width: 243px; height: 1px; }

  .identity {
    position: absolute;
    left: 30px;
    top: 133px;
    height: 158px;
    writing-mode: vertical-rl;
    transform: rotate(180deg);
    color: var(--bronze);
    display: flex;
    flex-direction: column;
    gap: 6px;
  }
  .identity__name {
    font-family: "Bodoni Moda", serif;
    font-weight: 600;
    font-size: 16px;
    letter-spacing: 0.02em;
    text-transform: uppercase;
  }
  .identity__role {
    font-family: "Gilda Display", serif;
    font-size: 12px;
    letter-spacing: 0.04em;
  }

  .contact {
    position: absolute;
    left: 334px;
    font-family: "Gilda Display", serif;
    font-size: 13.5px;
    letter-spacing: 0.06em;
    color: var(--bronze);
    line-height: 1;
    white-space: nowrap;
  }
  .contact--web     { top: 32px; }
  .contact--phone   { top: 139px; }
  .contact--email   { top: 165px; }
  .contact--address { top: 247px; line-height: 25px; }

  .brand {
    position: absolute;
    left: 0;
    right: 0;
    top: 128px;
    text-align: center;
    font-family: "Gilda Display", serif;
    font-size: 58px;
    letter-spacing: 0.02em;
    color: var(--logo-ink);
    line-height: 1;
  }
</style>
</head>
<body>
  <section class="card card--front" aria-label="Card front">
    <span class="frame-line frame-line--top"></span>
    <span class="frame-line frame-line--side"></span>
    <span class="frame-line frame-line--bottom"></span>

    <div class="identity">
      <span class="identity__name">Nora L. Castell</span>
      <span class="identity__role">Director</span>
    </div>

    <p class="contact contact--web">www.lashverastudio.example</p>
    <p class="contact contact--phone">310.555.0142</p>
    <p class="contact contact--email">lashverabh@example.com</p>
    <p class="contact contact--address">4720 N.Alder Crest Ave<br>Linden Vale , CA 91827</p>
  </section>

  <section class="card card--back" aria-label="Card back">
    <p class="brand">Lashvera</p>
  </section>
</body>
</html>
```